High value cover design for an A4 ideation pad.

The product is NOT A BOOK.

It's an A4 ideation pad for professionals, designers and creators who handwrite their ideas. Visualise creators like Milo Varnet, Owen Plaskit and Gregor Lunwick in your mind's eye.

I'm looking for a cover design for the ideation pad. Both front and back.

It should look, feel and convey the following.

--> A handcrafted product experience

--> High value & Elegance

--> Inspiration

Mandatory --> See Uploaded Files --> Files 1, 5 & 6

Target Market(s)

- Designers

-Creative Professionals

- Entrepreneurs

who handwrite their ideas. Visualise creators like Milo Varnet, Owen Plaskit and Gregor Lunwick in your mind's eye.

Industry/Entity Type

Stationary

Font styles to use
Script
Other font styles liked:
• Calligraphy

Colors
fbed22

Requirements
Must have
• Title text - Quiet Kettle Notes

-Text in gold on brown leather background to convey high value for the front cover.

--> High value & Elegance

--> Inspiration

--> Should compel the customers to pick up and own the idea pad
Nice to have
• That's my take but other ideas are welcome
Should not have
• Must not convey

- low value

```html
<!DOCTYPE html>
<html lang="en">
<head>
<meta charset="utf-8">
<title>Quiet Kettle Notes – Ideation Pad Covers</title>
<link rel="stylesheet" href="https://fonts.googleapis.com/css2?family=Allura&display=swap">
<style>
  :root {
    --page-bg: #ffffff;
    --leather-base: #d9793a;
    --leather-light: #e38b48;
    --leather-dark: #c96a2c;
    --gold-light: #f6dca0;
    --gold-mid: #e2b96a;
    --gold-deep: #c8964a;
    --wire: #5a5a5c;
    --wire-dark: #333335;
  }
  * { margin: 0; padding: 0; box-sizing: border-box; }
  html, body {
    width: 1200px;
    height: 969px;
    overflow: hidden;
    background: var(--page-bg);
  }
  .stage {
    position: relative;
    width: 1200px;
    height: 969px;
  }
  .pad {
    position: absolute;
    width: 552px;
    height: 768px;
  }
  .pad--back  { left: 570px; top: 141px; z-index: 1; }
  .pad--front { left: 120px; top: 66px; z-index: 2; }

  .cover {
    position: absolute;
    inset: 0;
    overflow: hidden;
    box-shadow: 2px 3px 6px rgba(0, 0, 0, 0.25);
    background:
      radial-gradient(ellipse 60% 40% at 30% 25%, var(--leather-light) 0%, transparent 70%),
      radial-gradient(ellipse 50% 35% at 75% 70%, var(--leather-dark) 0%, transparent 75%),
      radial-gradient(ellipse 45% 30% at 20% 80%, var(--leather-light) 0%, transparent 70%),
      radial-gradient(ellipse 40% 30% at 85% 20%, var(--leather-dark) 0%, transparent 70%),
      var(--leather-base);
  }
  .leather-grain {
    position: absolute;
    inset: 0;
    width: 100%;
    height: 100%;
    opacity: 0.35;
    mix-blend-mode: soft-light;
  }

  .spiral {
    position: absolute;
    left: 0;
    top: -17px;
    width: 552px;
    height: 52px;
    z-index: 3;
  }
  .spiral .ring {
    fill: none;
    stroke: var(--wire);
    stroke-width: 3;
    stroke-linecap: round;
  }
  .spiral .hole { fill: var(--wire-dark); }

  .figure-art {
    position: absolute;
    left: 46px;
    top: 120px;
    width: 392px;
    height: 502px;
    border-radius: 46% 40% 30% 30%;
    background: radial-gradient(ellipse at 55% 45%, rgba(246, 220, 160, 0.22) 0%, rgba(226, 185, 106, 0.1) 55%, transparent 78%);
  }

  .title {
    position: absolute;
    padding: 0.25em 0.3em;
    font-family: "Allura", cursive;
    font-weight: 400;
    color: var(--gold-mid);
    background: linear-gradient(160deg, var(--gold-light) 0%, var(--gold-mid) 45%, var(--gold-deep) 100%);
    -webkit-background-clip: text;
    background-clip: text;
    -webkit-text-fill-color: transparent;
    line-height: 0.85;
    white-space: nowrap;
  }
  .title span { display: block; }
  .title .title__small { font-size: 0.5em; }

  .cover--front .title {
    left: 278px;
    top: 332px;
    font-size: 80px;
  }
  .cover--front .title__first { padding-left: 0.62em; }
  .cover--front .title__small { padding-left: 1.5em; }

  .cover--back .title {
    left: 205px;
    top: 296px;
    font-size: 62px;
  }
  .cover--back .title__row { display: block; }
  .cover--back .title__row span { display: inline; }
  .cover--back .title__first { padding-left: 0.1em; }
</style>
</head>
<body>
  <main class="stage">
    <section class="pad pad--back" aria-label="Back cover">
      <div class="cover cover--back">
        <svg class="leather-grain" aria-hidden="true">
          <filter id="grain-back"><feTurbulence type="fractalNoise" baseFrequency="0.9" numOctaves="2" seed="4"/><feColorMatrix type="saturate" values="0"/></filter>
          <rect width="100%" height="100%" filter="url(#grain-back)"/>
        </svg>
        <h2 class="title">
          <span class="title__first">Quiet</span>
          <span class="title__row"><span class="title__small">Kettle </span><span class="title__last">Notes</span></span>
        </h2>
      </div>
      <svg class="spiral" viewBox="0 0 552 52" aria-hidden="true">
        <g id="spiral-set">
          <g transform="translate(42 0)"><path class="ring" d="M6 48 C-4 40 -4 8 6 4 C14 1 16 10 15 18"/><path class="ring" d="M14 48 C4 40 4 8 14 4 C22 1 24 10 23 18"/><rect class="hole" x="6" y="46" width="10" height="4" rx="2"/></g>
          <g transform="translate(78 0)"><path class="ring" d="M6 48 C-4 40 -4 8 6 4 C14 1 16 10 15 18"/><path class="ring" d="M14 48 C4 40 4 8 14 4 C22 1 24 10 23 18"/><rect class="hole" x="6" y="46" width="10" height="4" rx="2"/></g>
          <g transform="translate(114 0)"><path class="ring" d="M6 48 C-4 40 -4 8 6 4 C14 1 16 10 15 18"/><path class="ring" d="M14 48 C4 40 4 8 14 4 C22 1 24 10 23 18"/><rect class="hole" x="6" y="46" width="10" height="4" rx="2"/></g>
          <g transform="translate(150 0)"><path class="ring" d="M6 48 C-4 40 -4 8 6 4 C14 1 16 10 15 18"/><path class="ring" d="M14 48 C4 40 4 8 14 4 C22 1 24 10 23 18"/><rect class="hole" x="6" y="46" width="10" height="4" rx="2"/></g>
          <g transform="translate(186 0)"><path class="ring" d="M6 48 C-4 40 -4 8 6 4 C14 1 16 10 15 18"/><path class="ring" d="M14 48 C4 40 4 8 14 4 C22 1 24 10 23 18"/><rect class="hole" x="6" y="46" width="10" height="4" rx="2"/></g>
          <g transform="translate(222 0)"><path class="ring" d="M6 48 C-4 40 -4 8 6 4 C14 1 16 10 15 18"/><path class="ring" d="M14 48 C4 40 4 8 14 4 C22 1 24 10 23 18"/><rect class="hole" x="6" y="46" width="10" height="4" rx="2"/></g>
          <g transform="translate(258 0)"><path class="ring" d="M6 48 C-4 40 -4 8 6 4 C14 1 16 10 15 18"/><path class="ring" d="M14 48 C4 40 4 8 14 4 C22 1 24 10 23 18"/><rect class="hole" x="6" y="46" width="10" height="4" rx="2"/></g>
          <g transform="translate(294 0)"><path class="ring" d="M6 48 C-4 40 -4 8 6 4 C14 1 16 10 15 18"/><path class="ring" d="M14 48 C4 40 4 8 14 4 C22 1 24 10 23 18"/><rect class="hole" x="6" y="46" width="10" height="4" rx="2"/></g>
          <g transform="translate(330 0)"><path class="ring" d="M6 48 C-4 40 -4 8 6 4 C14 1 16 10 15 18"/><path class="ring" d="M14 48 C4 40 4 8 14 4 C22 1 24 10 23 18"/><rect class="hole" x="6" y="46" width="10" height="4" rx="2"/></g>
          <g transform="translate(366 0)"><path class="ring" d="M6 48 C-4 40 -4 8 6 4 C14 1 16 10 15 18"/><path class="ring" d="M14 48 C4 40 4 8 14 4 C22 1 24 10 23 18"/><rect class="hole" x="6" y="46" width="10" height="4" rx="2"/></g>
          <g transform="translate(402 0)"><path class="ring" d="M6 48 C-4 40 -4 8 6 4 C14 1 16 10 15 18"/><path class="ring" d="M14 48 C4 40 4 8 14 4 C22 1 24 10 23 18"/><rect class="hole" x="6" y="46" width="10" height="4" rx="2"/></g>
          <g transform="translate(438 0)"><path class="ring" d="M6 48 C-4 40 -4 8 6 4 C14 1 16 10 15 18"/><path class="ring" d="M14 48 C4 40 4 8 14 4 C22 1 24 10 23 18"/><rect class="hole" x="6" y="46" width="10" height="4" rx="2"/></g>
          <g transform="translate(474 0)"><path class="ring" d="M6 48 C-4 40 -4 8 6 4 C14 1 16 10 15 18"/><path class="ring" d="M14 48 C4 40 4 8 14 4 C22 1 24 10 23 18"/><rect class="hole" x="6" y="46" width="10" height="4" rx="2"/></g>
          <g transform="translate(510 0)"><path class="ring" d="M6 48 C-4 40 -4 8 6 4 C14 1 16 10 15 18"/><path class="ring" d="M14 48 C4 40 4 8 14 4 C22 1 24 10 23 18"/><rect class="hole" x="6" y="46" width="10" height="4" rx="2"/></g>
        </g>
      </svg>
    </section>

    <section class="pad pad--front" aria-label="Front cover">
      <div class="cover cover--front">
        <svg class="leather-grain" aria-hidden="true">
          <filter id="grain-front"><feTurbulence type="fractalNoise" baseFrequency="0.9" numOctaves="2" seed="9"/><feColorMatrix type="saturate" values="0"/></filter>
          <rect width="100%" height="100%" filter="url(#grain-front)"/>
        </svg>
        <div class="figure-art" role="img" aria-label="Gold foil line drawing of a leaping figure with arms outstretched"></div>
        <h1 class="title">
          <span class="title__first">Quiet</span>
          <span class="title__small">Kettle</span>
          <span class="title__last">Notes</span>
        </h1>
      </div>
      <svg class="spiral" viewBox="0 0 552 52" aria-hidden="true">
        <use href="#spiral-set" transform="translate(-16 0)"/>
      </svg>
    </section>
  </main>
</body>
</html>
```